BLS Business Card 2018

Larkmere Chiropractic. We have two locations that we want to advertise on the same card. Brightvale OrthoCore campus address: 3815 Pellham Dr., Suite 240, Flowood, MS 39417. Madison address: 246 Willowmere Dr., Building D., Madison, MS 39284. website: www.drlarkmere-example.com. o:(601)555-0147 f:(601)555-0183

Target Market(s)

Health care decision makers: primary care doctors and mothers

Contact Information for Business Card

I have no idea; up for any suggestions and I'd do much better picking from examples versus describing what I'm looking for. We are in a very high end location and would like the cards to look really sharp.

Requirements
Must have
• My name, Martin R Belvane, D.C.

```html
<!DOCTYPE html>
<html lang="en">
<head>
<meta charset="utf-8">
<title>Larkmere Chiropractic — Business Card</title>
<link rel="stylesheet" href="https://fonts.googleapis.com/css2?family=Roboto:wght@400;500&family=Roboto+Condensed:wght@700&display=swap">
<style>
  :root {
    --backdrop: #e8e5e1;
    --card-light: #f5f5f4;
    --card-dark: #2a2a2a;
    --ink-strong: #111111;
    --ink-body: #545454;
    --ink-soft: #9a9a9a;
    --ink-reverse: #f2f2f2;
    --divider: #8f8f8f;
  }
  * { margin: 0; padding: 0; box-sizing: border-box; }
  html, body {
    width: 1200px;
    height: 960px;
    overflow: hidden;
    background: var(--backdrop);
    font-family: "Roboto", Arial, sans-serif;
  }
  .canvas {
    position: relative;
    width: 1200px;
    height: 960px;
  }
  .card {
    position: absolute;
    width: 600px;
    box-shadow: 0 3px 10px rgba(0,0,0,0.18);
  }
  .card--front {
    left: 314px;
    top: 113px;
    height: 317px;
    background: var(--card-light);
  }
  .card--back {
    left: 312px;
    top: 472px;
    height: 343px;
    background: var(--card-dark);
  }

  /* Brand name block */
  .brand {
    position: absolute;
    display: flex;
    align-items: center;
    gap: 12px;
    font-family: "Roboto", Arial, sans-serif;
    font-weight: 400;
    text-transform: uppercase;
    line-height: 1.05;
  }
  .brand__dot {
    width: 10px;
    height: 10px;
    border-radius: 50%;
    flex: none;
  }
  .card--front .brand {
    left: 40px;
    top: 133px;
    color: var(--ink-strong);
    font-size: 22px;
    letter-spacing: 1px;
  }
  .card--front .brand__dot { background: var(--ink-strong); }
  .card--back .brand {
    left: 0;
    right: 0;
    top: 122px;
    justify-content: center;
    color: var(--ink-reverse);
    font-size: 34px;
    letter-spacing: 1.5px;
  }
  .card--back .brand__dot { background: var(--ink-reverse); width: 14px; height: 14px; }

  .divider {
    position: absolute;
    left: 308px;
    top: 55px;
    width: 1px;
    height: 222px;
    background: linear-gradient(to bottom, rgba(143,143,143,0), var(--divider) 20%, var(--divider) 80%, rgba(143,143,143,0));
  }

  .contact {
    position: absolute;
    left: 332px;
    top: 55px;
    color: var(--ink-body);
    font-size: 14.5px;
    line-height: 18.5px;
  }
  .contact__name {
    font-family: "Roboto Condensed", "Arial Narrow", sans-serif;
    font-weight: 700;
    font-size: 21px;
    line-height: 26px;
    color: var(--ink-strong);
    margin-bottom: 7px;
  }
  .contact__address { margin-bottom: 7px; }
  .contact__lines { list-style: none; margin-top: 8px; }
  .contact__lines li {
    display: flex;
    align-items: center;
    gap: 8px;
    height: 19.5px;
  }
  .contact__icon { width: 14px; height: 14px; flex: none; fill: var(--ink-strong); }

  .web {
    position: absolute;
    left: 0;
    right: 0;
    top: 281px;
    text-align: center;
    color: var(--ink-reverse);
    font-size: 14px;
    letter-spacing: 4.4px;
    text-transform: uppercase;
  }
</style>
</head>
<body>
<main class="canvas">

  <section class="card card--front" aria-label="Card front">
    <div class="brand">
      <span class="brand__dot"></span>
      <span>Larkmere<br>Chiropractic</span>
    </div>

    <div class="divider"></div>

    <div class="contact">
      <h1 class="contact__name">MARTIN R BELVANE, D.C.</h1>
      <p class="contact__address">Brightvale OrthoCore campus :<br>3815 Pellham Dr., Suite 240<br>Flowood, MS 39417.</p>
      <p class="contact__address">Madison address:<br>246 Willowmere Dr., Building D.<br>Madison, MS 39284.</p>
      <ul class="contact__lines">
        <li>
          <svg class="contact__icon" viewBox="0 0 16 16" aria-label="Phone"><path d="M3.6 1.2l2.3 2.6c.3.4.3.9 0 1.2L4.8 6.2c.9 2 2.6 3.7 4.9 4.9l1.2-1.1c.3-.3.9-.3 1.2 0l2.6 2.3c.4.3.4.9 0 1.3l-1.3 1.3c-.6.6-1.6.8-2.4.4C6.6 13.4 2.6 9.4.8 5.1.4 4.3.6 3.3 1.2 2.7L2.4 1.2c.3-.4.9-.4 1.2 0z"/></svg>
          <span>(601)555-0147</span>
        </li>
        <li>
          <svg class="contact__icon" viewBox="0 0 16 16" aria-label="Fax"><rect x="4" y="1" width="8" height="4"/><rect x="1" y="6" width="14" height="6" rx="1"/><rect x="4" y="10" width="8" height="5" fill="#f5f5f4" stroke="#111" stroke-width="1.2"/></svg>
          <span>(601)555-0183</span>
        </li>
        <li>
          <svg class="contact__icon" viewBox="0 0 16 16" aria-label="Website"><circle cx="8" cy="8" r="7"/><path d="M5 4.5c1.5-.5 2.5.5 2 1.8-.4 1-1.8.8-2 2.2-.2 1.2 1 1.5 1 2.8M10.5 9.5c.8.2 1.5 1 1.2 2.2" stroke="#f5f5f4" stroke-width="1.3" fill="none"/></svg>
          <span>www.drlarkmere-example.com</span>
        </li>
      </ul>
    </div>
  </section>

  <section class="card card--back" aria-label="Card back">
    <div class="brand">
      <span class="brand__dot"></span>
      <span>Larkmere<br>Chiropractic</span>
    </div>
    <p class="web">www.drlarkmere-example.com</p>
  </section>

</main>
</body>
</html>
```